MyName is TapLedger .... Killer of Business Cards!!! WANT a KickAss Design Landing Page :)

How 'TapLedger' works:
- with a unique name for each country, like a personalise car plate number
- our platform links through a 'Quick Text' keyword short code
- TapLedger platform will respond with downloaded ready full contact business file link
- this is designed to be downloaded in just '3 clicks' into your Contacts Folder
- any changes,,updates, images, online profiles can be made in real time updates
- TapLedger provides a backend login to manage individual account and is ready
Enterprise model for larger staff companies
- platform is international ready and have launched
Australia, in September 2019.

Yes, your whole business card and online profile in '3' simple clicks. No '20-30 mins' of typing the business card contacts details into mobile phones.
** Fact: 88% of business cards are lost of thrown out within 7 days.
(https://www.plumfinchstats.com/business-card-statistics.html) **

NZ ClipStream
https://vidhost.example/q7Rt2LmP9xZ

**current websites are www.tapledge.co.nz www.taplink.com.au www.tapledgerau.com www.tapledgerus.com **

Target Market(s)

Anybody who uses a business card, from trades person, real estate agents, consultants, bankers (in NZ/AU with have plumbers, financial advisors, real estate agents, mortgage brokers, sports agents, Telcos etc etc)

Industry/Entity Type

Business Software

Coding

Coded - Design and coding required

Number of Pages Required

4 page

Font styles to use
Other font styles liked:
• libre franklin black

Requirements
Must have
• TapLedger a simple 'in delivery' and smart 'in innovation' solution so our message is Simple, Clear and Inquisitive. We would like a converting landing page because we are selling Nimble Cloud Suite at low-entry cost and no-contract. IWe want to direct clients to a name reservation platform to a virtual business card that uses our Nimble Core Engine. We will require some code at the back to link the name reservation and sign up source code(javascript). This web/landing page fresh page is required because we have recently changed our marketing strategy to be purely digital marketing in Chatterbook and Snapgrid Ads from now on. We would like this to be exciting graphically to grab attention, inquisitive enough to check your name availability and follow through with call to action with the right colours and graphics images. We plan to test the right pitch offering until we get the markets feedback on the best offering/re-design and then push harder with more CB and SG Ads. ( **we plan to continue multiple regular campaigns as the business has now change our strategy due to covid-19 and we will focus mainly on direct to consumers**)

Also:
2 buttons: Signup and a Check availability little form to allow a java script to be added/HTML5/CB advertising/Super Inviting to check 'YOUR UNIQUE NAME' is available. Then clicking the to reserve the name to purchase our Quick Text/Eco-Friendly/Relevant to todays tech and Low Cost service. We will be offering Promo codes for each campaign.
No Apps. Works with SMS, any smartphone, country specific, enterprise ready, and CONTACTLESS ....
Nice to have
• Personal feeling. Unique choice of 'your name' as this is your business and social profile in one. Strong independent images and confident to share with anybody their profile by just sharing their name.
Should not have
• Open currently....

```html
<!DOCTYPE html>
<html lang="en">
<head>
<meta charset="utf-8">
<title>TapLedger – Share Your Business Contact in One Quick Text</title>
<link rel="stylesheet" href="https://fonts.googleapis.com/css2?family=Libre+Franklin:ital,wght@0,400;0,500;0,600;0,700;0,800;0,900;1,400&family=Montserrat:wght@700;800&display=swap">
<style>
:root{
  --teal:#1a8a8c;
  --teal-dark:#0f6c70;
  --teal-light:#22a19e;
  --navy:#232d5e;
  --navy-deep:#1e2a63;
  --navy-card:#263470;
  --ink:#3b3f4a;
  --muted:#6c717c;
  --gray-band:#f2f3f5;
  --gold:#e0b23c;
  --white:#ffffff;
}
*{box-sizing:border-box;margin:0;padding:0}
html,body{width:1200px;height:4758px;overflow:hidden;background:var(--white)}
body{position:relative;font-family:"Libre Franklin",Arial,sans-serif;color:var(--ink)}
.abs{position:absolute}
.backdrop{position:absolute;left:0;top:0}
/* header */
.brand{position:absolute;display:flex;align-items:center;gap:10px;font-family:"Libre Franklin",sans-serif;font-weight:800;color:var(--navy);letter-spacing:.5px;white-space:nowrap}
.brand-dot{width:22px;height:22px;border-radius:50%;background:var(--teal)}
.nav{position:absolute;top:56px;left:355px;font-size:12px;font-weight:700;text-transform:uppercase;color:#333}
.nav a{color:inherit;text-decoration:none;position:absolute;white-space:nowrap}
.nav a.active{color:var(--teal)}
.btn{position:absolute;display:flex;align-items:center;justify-content:center;border-radius:26px;color:#fff;font-weight:600;text-decoration:none}
.btn-teal{background:var(--teal)}
.btn-navy{background:var(--navy-deep)}
/* hero */
.hero-title{position:absolute;top:432px;left:0;width:1200px;text-align:center;font-family:"Montserrat",sans-serif;font-weight:800;font-size:82px;color:#fff;letter-spacing:1px}
.hero-sub{position:absolute;top:532px;left:0;width:1200px;text-align:center;font-size:28px;line-height:42px;color:#fff;font-weight:400}
.dots{position:absolute;top:846px;left:577px;display:flex;gap:8px}
.dots span{width:10px;height:10px;border-radius:50%;background:#fff}
.dots span.on{background:var(--teal-light)}
/* section heads */
.sec-title{position:absolute;left:0;width:1200px;text-align:center;font-size:34px;font-weight:500;color:var(--navy)}
.sec-title em{font-style:normal;color:var(--teal)}
.sec-sub{position:absolute;left:0;width:1200px;text-align:center;font-size:13px;color:#555}
/* benefits */
.benefit-icon{position:absolute;width:88px;height:88px;border:2.5px solid var(--teal);border-radius:50%;display:flex;align-items:center;justify-content:center;color:var(--teal)}
.benefit-text{position:absolute;width:240px}
.benefit-text h3{font-size:18px;font-weight:500;color:var(--teal);margin-bottom:12px}
.benefit-text p{font-size:12px;line-height:21px;color:#555}
.benefit-text.right{text-align:right}
.phone-frame{position:absolute;left:478px;top:1103px;width:243px;height:492px;border:7px solid #111;border-radius:34px;background:linear-gradient(#fff,#eef3f8)}
.phone-notch{position:absolute;left:64px;top:-2px;width:102px;height:18px;background:#111;border-radius:0 0 12px 12px}
/* partners */
.partner-badge{position:absolute;left:199px;top:1914px;width:206px;height:206px;border-radius:50%;background:#fff;display:flex;align-items:center;justify-content:center;gap:8px}
.partner-name{font-size:27px;font-weight:700;color:var(--teal)}
.partner-copy{position:absolute;left:440px;top:1950px;width:570px;font-size:13px;line-height:27.5px;color:#fff}
/* plans */
.device{position:absolute;border-radius:30px;border:6px solid #e7e9ee;box-shadow:0 6px 18px rgba(0,0,0,.12)}
.plan h3{position:absolute;font-size:30px;font-weight:500;color:var(--navy)}
.plan .offer{position:absolute;font-size:18px;line-height:31px;color:var(--teal);font-weight:500}
.plan ul{position:absolute;list-style:none}
.plan li{display:flex;align-items:center;gap:14px;font-size:16px;color:#333;height:51px}
.plan li svg{flex:none}
/* testimonials */
.quote-card{position:absolute;top:3950px;width:314px;height:226px;background:var(--navy-card);padding:20px 22px}
.quote-head{display:flex;align-items:center;gap:10px;margin-bottom:16px}
.quote-mark{font-family:Georgia,serif;font-size:34px;font-weight:700;color:#fff;line-height:20px;height:20px}
.stars{display:flex;gap:3px}
.quote-card p{font-size:11.5px;line-height:23px;font-style:italic;color:#fff;text-align:justify}
.client{position:absolute;top:4200px;display:flex;align-items:center;gap:16px}
.avatar{width:72px;height:72px;border-radius:50%;background:radial-gradient(circle at 50% 40%,#c79a7a,#6b4a3a)}
.client h4{font-size:19px;font-weight:500;color:#fff}
.client span{font-size:12px;color:#dfe3f0}
/* footer */
.foot-nav{position:absolute;top:4585px;left:0;width:1200px;display:flex;justify-content:center;gap:40px;font-size:12px;font-weight:700;text-transform:uppercase;color:#333}
.pay-cards{position:absolute;top:4651px;left:503px;display:flex;gap:6px}
.pay-cards span{width:44px;height:28px;border-radius:3px;background:#cfd3dc}
.copyright{position:absolute;top:4700px;left:0;width:1200px;text-align:center;font-size:13px;color:#333}
</style>
</head>
<body>

<svg class="backdrop" width="1200" height="4758" viewBox="0 0 1200 4758" aria-hidden="true">
  <defs>
    <linearGradient id="partnerBand" x1="0" y1="0" x2="0" y2="1">
      <stop offset="0" stop-color="#1f9b98"/>
      <stop offset="1" stop-color="#0e6a70"/>
    </linearGradient>
  </defs>
  <path d="M0,1680 Q600,1828 1200,1680 L1200,2140 Q600,2198 0,2140 Z" fill="url(#partnerBand)"/>
  <path d="M0,2990 Q600,2930 1200,2990 L1200,3800 L0,3800 Z" fill="var(--gray-band)"/>
  <path d="M0,3650 C420,3800 820,3720 1200,3765 L1200,4329 Q600,4440 0,4329 Z" fill="var(--navy-deep)"/>
</svg>

<svg class="abs" style="left:0;top:122px" width="1200" height="763" viewBox="0 122 1200 763" role="img" aria-label="Photo of four friends standing against a wooden wall, smiling at their smartphones">
  <defs>
    <linearGradient id="heroTone" x1="0" y1="0" x2="0" y2="1">
      <stop offset="0" stop-color="#6a5a4c"/>
      <stop offset="0.55" stop-color="#3e3a3c"/>
      <stop offset="1" stop-color="#23293a"/>
    </linearGradient>
  </defs>
  <path d="M0,122 L1200,122 L1200,738 Q600,1030 0,738 Z" fill="url(#heroTone)"/>
</svg>

<header>
  <div class="brand" style="left:112px;top:40px;font-size:30px"><span class="brand-dot"></span>TapLedger</div>
  <nav class="nav">
    <a class="active" style="left:0">Home</a>
    <a style="left:80px">Partners</a>
    <a style="left:190px">Benefits</a>
    <a style="left:296px">Plans</a>
    <a style="left:382px">Testimonials</a>
    <a style="left:522px">Contact Us</a>
  </nav>
  <a class="btn btn-teal" style="left:977px;top:39px;width:112px;height:46px;font-size:14px">SIGNUP</a>
</header>

<section class="hero">
  <h1 class="hero-title">TAPLEDGER</h1>
  <p class="hero-sub">Instantly Share All Your Business Contact<br>Details with 1 ‘QUICK TEXT’ SMS</p>
  <a class="btn btn-teal" style="left:495px;top:640px;width:211px;height:50px;font-size:17px;font-weight:500">Check Availability</a>
  <div class="dots"><span></span><span class="on"></span><span></span></div>
</section>

<section class="benefits">
  <h2 class="sec-title" style="top:950px">Simple <em>Benefits Are</em></h2>
  <p class="sec-sub" style="top:1010px">FoundBack™ is the World's Largest Global Recovery company which helps return lost items</p>

  <div class="benefit-icon" style="left:110px;top:1106px"><svg width="40" height="40" viewBox="0 0 40 40" fill="none" stroke="currentColor" stroke-width="2"><rect x="8" y="6" width="24" height="28" rx="2"/><path d="M13 26 l5-6 4 4 6-8"/></svg></div>
  <div class="benefit-text" style="left:220px;top:1112px"><h3>Logical</h3><p>Everybody has a mobile phone and every phone can txt/sms.</p></div>

  <div class="benefit-icon" style="left:110px;top:1240px"><svg width="40" height="40" viewBox="0 0 40 40" fill="none" stroke="currentColor" stroke-width="2"><circle cx="20" cy="10" r="4"/><path d="M14 34 V20 a6 6 0 0 1 12 0 V34"/></svg></div>
  <div class="benefit-text" style="left:220px;top:1246px"><h3>Professional</h3><p>Your customers / potential customers impressed with your innovation.</p></div>

  <div class="benefit-icon" style="left:110px;top:1374px"><svg width="40" height="40" viewBox="0 0 40 40" fill="none" stroke="currentColor" stroke-width="2"><ellipse cx="20" cy="9" rx="11" ry="4"/><path d="M9 9 V31 c0 5 22 5 22 0 V9 M9 20 c0 5 22 5 22 0"/></svg></div>
  <div class="benefit-text" style="left:220px;top:1380px"><h3>Data Safe</h3><p>All data is held on a secure Cirrus Host infrastructure in Sydney</p></div>

  <div class="benefit-icon" style="left:110px;top:1508px"><svg width="40" height="40" viewBox="0 0 40 40" fill="none" stroke="currentColor" stroke-width="2"><rect x="6" y="14" width="28" height="18" rx="2"/><circle cx="20" cy="23" r="4"/><path d="M20 4 v6"/></svg></div>
  <div class="benefit-text" style="left:220px;top:1514px"><h3>Secure Payment</h3><p>Back by the global PayRail payment gate as a PCI Level One Service Provider.</p></div>

  <div class="phone-frame"><div class="phone-notch"></div>
    <div class="brand" style="left:24px;top:205px;font-size:27px"><span class="brand-dot" style="width:18px;height:18px"></span>TapLedger</div>
  </div>

  <div class="benefit-text right" style="left:745px;top:1112px"><h3>Environment</h3><p>No use of business cards, you no longer need to have cards printed, thus</p></div>
  <div class="benefit-icon" style="left:1000px;top:1106px"><svg width="40" height="40" viewBox="0 0 40 40" fill="none" stroke="currentColor" stroke-width="2"><path d="M20 30 C10 24 10 12 20 6 C30 12 30 24 20 30 Z M20 30 V36"/></svg></div>

  <div class="benefit-text right" style="left:745px;top:1246px"><h3>Ease</h3><p>So simple to share and retrieve your TapLedger.</p></div>
  <div class="benefit-icon" style="left:1000px;top:1240px"><svg width="40" height="40" viewBox="0 0 40 40" fill="none" stroke="currentColor" stroke-width="2"><rect x="7" y="6" width="26" height="28" rx="2"/><path d="M12 13 h16 M12 19 h16 M12 25 h10"/></svg></div>

  <div class="benefit-text right" style="left:745px;top:1380px"><h3>Sales</h3><p>May increase your sales by word of mouth, added to your advertising</p></div>
  <div class="benefit-icon" style="left:1000px;top:1374px"><svg width="40" height="40" viewBox="0 0 40 40" fill="none" stroke="currentColor" stroke-width="2"><path d="M8 34 v-6 M16 34 v-10 M24 34 v-8 M32 34 v-14 M8 20 l8-6 8 4 8-10"/></svg></div>

  <div class="benefit-text right" style="left:745px;top:1514px"><h3>Cost</h3><p>The service is less per year than the persons cost in business cards</p></div>
  <div class="benefit-icon" style="left:1000px;top:1508px;font-weight:700;font-size:22px">$$$</div>
</section>

<section class="partners">
  <h2 class="sec-title" style="top:1808px;color:#fff">Our Partners</h2>
  <p class="sec-sub" style="top:1862px;color:#fff">FoundBack™ is the World's Largest Global Recovery company which helps return lost items</p>
  <div class="partner-badge"><span class="brand-dot"></span><span class="partner-name">FoundBack</span></div>
  <p class="partner-copy">FoundBack™ is the World's Largest Global Recovery company which helps return lost items to their rightful owners. With over an 80% recovery rate, FoundBack recovery tags help identify and protect all types of portable items ranging from cell phones to laptops, keys to luggage and even cats &amp; dogs. FoundBack's system is simple, cove nient, confidential and rewarding!</p>
</section>

<section class="plans">
  <h2 class="sec-title" style="top:2280px">Plans For <em>Everyone</em></h2>
  <p class="sec-sub" style="top:2340px">FoundBack™ is the World's Largest Global Recovery company which helps return lost items</p>

  <div class="plan">
    <div class="device" role="img" aria-label="Smartphone showing a downloaded contact card ready to open in Contacts" style="left:210px;top:2418px;width:232px;height:537px;background:linear-gradient(#f4f5f8,#c9cbe0 50%,#eef0f5)"></div>
    <h3 style="left:518px;top:2474px">Personal Plan</h3>
    <p class="offer" style="left:518px;top:2527px">Provides for one keyword and one personal TapLedger.<br>For $4.99 + gst / month</p>
    <ul style="left:518px;top:2612px">
      <li><svg width="16" height="14" viewBox="0 0 16 14"><path d="M2 7 l4 4 8-9" fill="none" stroke="#222" stroke-width="2.5"/></svg>Sed ut perspiciatis unde omnis iste natus error sit</li>
      <li><svg width="16" height="14" viewBox="0 0 16 14"><path d="M2 7 l4 4 8-9" fill="none" stroke="#222" stroke-width="2.5"/></svg>Sed ut perspiciatis unde omnis iste natus</li>
      <li><svg width="16" height="14" viewBox="0 0 16 14"><path d="M2 7 l4 4 8-9" fill="none" stroke="#222" stroke-width="2.5"/></svg>Nemo enim ipsam voluptatem quia voluptas</li>
      <li><svg width="16" height="14" viewBox="0 0 16 14"><path d="M2 7 l4 4 8-9" fill="none" stroke="#222" stroke-width="2.5"/></svg>Voluptatem accusantium doloremque laudantium</li>
    </ul>
    <a class="btn btn-teal" style="left:518px;top:2842px;width:157px;height:51px;font-size:17px;font-weight:500">Get Started</a>
  </div>

  <div class="plan">
    <h3 style="left:204px;top:3166px">Business Plan</h3>
    <p class="offer" style="left:204px;top:3219px">Provides for one personal and business keyword. For<br>$6.99 + gst / month</p>
    <ul style="left:204px;top:3304px">
      <li><svg width="16" height="14" viewBox="0 0 16 14"><path d="M2 7 l4 4 8-9" fill="none" stroke="#222" stroke-width="2.5"/></svg>Sed ut perspiciatis unde omnis iste natus error sit</li>
      <li><svg width="16" height="14" viewBox="0 0 16 14"><path d="M2 7 l4 4 8-9" fill="none" stroke="#222" stroke-width="2.5"/></svg>Sed ut perspiciatis unde omnis iste natus</li>
      <li><svg width="16" height="14" viewBox="0 0 16 14"><path d="M2 7 l4 4 8-9" fill="none" stroke="#222" stroke-width="2.5"/></svg>Nemo enim ipsam voluptatem quia voluptas</li>
      <li><svg width="16" height="14" viewBox="0 0 16 14"><path d="M2 7 l4 4 8-9" fill="none" stroke="#222" stroke-width="2.5"/></svg>Voluptatem accusantium doloremque laudantium</li>
    </ul>
    <a class="btn btn-navy" style="left:204px;top:3534px;width:158px;height:51px;font-size:17px;font-weight:500">Get Started</a>
    <div class="device" role="img" aria-label="Smartphone showing a blue payment card with a world map above a green pay button" style="left:760px;top:3110px;width:230px;height:535px;background:linear-gradient(#f3f4f7 8%,#7d96b3 15%,#2f5f95 30%,#dfe3e8 48%,#9ea2a8 95%)"></div>
  </div>
</section>

<section class="testimonials">
  <h2 class="sec-title" style="top:3806px;color:#fff">Our Clients love us!</h2>
  <p class="sec-sub" style="top:3866px;color:#dfe3f0">FoundBack™ is the World's Largest Global Recovery company which helps return lost items</p>

  <article class="quote-card" style="left:112px">
    <div class="quote-head"><span class="quote-mark">“</span><span class="stars"><svg width="80" height="14" viewBox="0 0 80 14"><g fill="none" stroke="var(--gold)" stroke-width="1.3"><path id="st" d="M7 1 l1.8 4 4.2.4-3.2 2.8 1 4.2L7 10.2 3.2 12.4l1-4.2L1 5.4l4.2-.4Z"/><use href="#st" x="16"/><use href="#st" x="32"/><use href="#st" x="48"/><use href="#st" x="64"/></g></svg></span></div>
    <p>This service gained me 10 listings for me over the past year! For me is the best and most powe rful tool available in the Real Estate industry. I often get caught out in social occas ions, bars, restaurants, expos, the beach, ever ywhere without a business card</p>
  </article>
  <article class="quote-card" style="left:443px">
    <div class="quote-head"><span class="quote-mark">“</span><span class="stars"><svg width="80" height="14" viewBox="0 0 80 14"><g fill="none" stroke="var(--gold)" stroke-width="1.3"><use href="#st"/><use href="#st" x="16"/><use href="#st" x="32"/><use href="#st" x="48"/><use href="#st" x="64"/></g></svg></span></div>
    <p>At HarbourLine Mortgages &amp; Insurance, we have found TapLedger to be an excellent tool for sharing our contact details. Simply asking them to txt 'Tobin' to 555 019 204 not only brings a smile to their face with the quirky innovation, but also professionalism and practicality.</p>
  </article>
  <article class="quote-card" style="left:774px">
    <div class="quote-head"><span class="quote-mark">“</span><span class="stars"><svg width="80" height="14" viewBox="0 0 80 14"><g fill="none" stroke="var(--gold)" stroke-width="1.3"><use href="#st"/><use href="#st" x="16"/><use href="#st" x="32"/><use href="#st" x="48"/><use href="#st" x="64"/></g></svg></span></div>
    <p>The really great thing I found with TapLedger is people's impressed reaction when they ask for a business card. Its also really handy if you run into someone when you're out and about. I recommend this service and it is very low to then my business cards run.</p>
  </article>

  <div class="client" style="left:112px"><div class="avatar" role="img" aria-label="Portrait photo of Mara Ellison"></div><div><h4>Mara Ellison</h4><span>Licensee Salesperson</span></div></div>
  <div class="client" style="left:443px"><div class="avatar" role="img" aria-label="Portrait photo of Tobin Reyes"></div><div><h4>Tobin Reyes</h4><span>Managing Director,</span></div></div>
  <div class="client" style="left:774px"><div class="avatar" role="img" aria-label="Portrait photo of Owen Castell"></div><div><h4>Owen Castell</h4><span>Managing Director,</span></div></div>
</section>

<footer>
  <div class="brand" style="left:468px;top:4500px;font-size:46px"><span class="brand-dot" style="width:30px;height:30px"></span>TapLedger</div>
  <nav class="foot-nav"><span>Home</span><span>Partners</span><span>Benefits</span><span>Plans</span><span>Testimonials</span><span>Contact Us</span></nav>
  <div class="pay-cards" aria-label="Accepted payment cards"><span></span><span></span><span></span><span></span></div>
  <p class="copyright">© Copyright -2020 TapLedger. All rights reserved.</p>
</footer>

</body>
</html>
```